Business Card Design Project

I need a business card designed from scratch. I have an existing logo that I can upload in Illustrator for modification or redesign.

The Company is called Query Lanterns http://querylanterns.com.au and we provide Search Engine Optimization services to Australian businesses. The current logo signifies an increase in visitors, profits etc...

There are no restrictions as to the redesign - colours, style etc are all open to change.

Cards will be full colour and one sided printed at http://www.cardmoxel.com.au so check their requirements for file format and sizes etc.

I will expect all original files upon completion of project.

Target Market(s)

Any business with a web site looking to improve their search engine rankings

Industry/Entity Type

Business

Requirements
Must have
• I like modern, sleek designs. Clean, not fussy, uncluttered.

```html
<!DOCTYPE html>
<html lang="en">
<head>
<meta charset="utf-8">
<title>Query Lanterns — Business Card</title>
<link href="https://fonts.googleapis.com/css2?family=Open+Sans:wght@400;600;700;800&display=swap" rel="stylesheet">
<style>
  :root {
    --backdrop: #d9d9d9;
    --card-black: #0b0b0b;
    --brand-red: #e31e24;
    --deep-red: #8e0d10;
    --brand-yellow: #f6c12c;
    --text-white: #ffffff;
  }
  * { margin: 0; padding: 0; box-sizing: border-box; }
  html, body {
    width: 1200px; height: 394px; overflow: hidden;
    background: var(--backdrop);
    font-family: "Open Sans", Arial, sans-serif;
  }
  .stage { position: relative; width: 1200px; height: 394px; }
  .card {
    position: absolute; top: 35px; height: 325px;
    background: var(--card-black);
    border-radius: 24px; overflow: hidden;
    box-shadow: 0 3px 10px rgba(0,0,0,0.35);
    color: var(--text-white);
  }
  .card--front { left: 15px; width: 570px; }
  .card--back { left: 618px; width: 567px; }
  .front-wave { position: absolute; inset: 0; width: 100%; height: 100%; }
  .brand-name {
    position: absolute; left: 185px; top: 58px;
    display: flex; align-items: center; gap: 12px;
    font-weight: 800; font-size: 40px; line-height: 1;
    color: var(--brand-red); letter-spacing: -0.5px;
  }
  .brand-dot {
    width: 18px; height: 18px; border-radius: 50%;
    background: var(--brand-yellow); flex: none;
  }
  .holder {
    position: absolute; left: 40px; top: 185px;
    font-size: 17px; white-space: nowrap;
  }
  .holder-name { font-weight: 700; font-size: 20px; }
  .contact-list {
    position: absolute; list-style: none;
    display: flex; flex-direction: column; gap: 5px;
    align-items: flex-end;
  }
  .contact-list li {
    display: flex; align-items: center; gap: 10px;
    font-size: 13.5px; line-height: 17px; white-space: nowrap;
  }
  .contact-list b { font-weight: 700; }
  .contact-list--phones { right: 25px; top: 233px; gap: 6px; }
  .contact-list--details { right: 22px; top: 213px; gap: 4px; }
  .contact-icon { width: 13px; height: 13px; flex: none; }
</style>
</head>
<body>
<main class="stage">
  <section class="card card--front" aria-label="Card front">
    <svg class="front-wave" viewBox="0 0 570 325" preserveAspectRatio="none" aria-hidden="true">
      <defs>
        <linearGradient id="redFade" x1="0" y1="0" x2="1" y2="0">
          <stop offset="0" stop-color="#e8232a"/>
          <stop offset="0.7" stop-color="#c4161c"/>
          <stop offset="1" stop-color="#8e0d10"/>
        </linearGradient>
      </defs>
      <path d="M0 205 C 90 230, 150 255, 250 215 C 360 170, 460 90, 570 60 L570 325 L0 325 Z" fill="var(--deep-red)"/>
      <path d="M0 215 C 90 240, 160 262, 260 222 C 370 178, 470 100, 570 82 L570 325 L0 325 Z" fill="var(--brand-yellow)"/>
      <path d="M0 221 C 90 246, 162 268, 262 228 C 372 184, 472 106, 570 89 L570 325 L0 325 Z" fill="url(#redFade)"/>
    </svg>

    <div class="brand-name"><span class="brand-dot"></span><span>Query Lanterns</span></div>

    <p class="holder"><span class="holder-name">Name</span> | Administrator</p>

    <ul class="contact-list contact-list--phones">
      <li>001-123-123456
        <svg class="contact-icon" viewBox="0 0 16 16" aria-label="Phone"><circle cx="8" cy="8" r="8" fill="var(--brand-red)"/><path d="M5 4c1 0 1.5 2 1 2.5l-.6.6c.5 1.2 1.3 2 2.5 2.5l.6-.6c.5-.5 2.5 0 2.5 1 0 1-1 1.8-2 1.6C6.5 11 4.9 9.5 4.4 6.9 4.2 5.5 4.5 4 5 4z" fill="#fff"/></svg></li>
      <li>001-123-123456
        <svg class="contact-icon" viewBox="0 0 16 16" aria-label="Fax"><circle cx="8" cy="8" r="8" fill="var(--brand-red)"/><rect x="5" y="4" width="6" height="3" fill="#fff"/><rect x="4" y="7" width="8" height="4" rx="1" fill="#fff"/><rect x="5.5" y="10" width="5" height="2" fill="#fff"/></svg></li>
      <li>001-123-123456
        <svg class="contact-icon" viewBox="0 0 16 16" aria-label="Mobile"><circle cx="8" cy="8" r="8" fill="var(--brand-red)"/><rect x="5.5" y="3.5" width="5" height="9" rx="1" fill="#fff"/><rect x="6.3" y="4.6" width="3.4" height="5.6" fill="var(--brand-red)"/></svg></li>
    </ul>
  </section>

  <section class="card card--back" aria-label="Card back">
    <ul class="contact-list contact-list--details">
      <li><span><b>Email.</b> hello@querylanterns.com.au</span>
        <svg class="contact-icon" viewBox="0 0 16 16" aria-label="Email"><circle cx="8" cy="8" r="8" fill="var(--brand-red)"/><circle cx="8" cy="8" r="3.6" fill="none" stroke="#fff" stroke-width="1.4"/><circle cx="8" cy="8" r="1.3" fill="#fff"/></svg></li>
      <li><span><b>Web.</b> www.querylanterns.com.au</span>
        <svg class="contact-icon" viewBox="0 0 16 16" aria-label="Website"><circle cx="8" cy="8" r="8" fill="var(--brand-red)"/><circle cx="8" cy="8" r="4" fill="none" stroke="#fff" stroke-width="1.1"/><path d="M4 8h8M8 4c-2 2.5-2 5.5 0 8M8 4c2 2.5 2 5.5 0 8" fill="none" stroke="#fff" stroke-width="0.9"/></svg></li>
      <li><span>25 Street Name, Road Name, State, Country Code</span>
        <svg class="contact-icon" viewBox="0 0 16 16" aria-label="Address"><circle cx="8" cy="8" r="8" fill="var(--brand-red)"/><path d="M8 3.8 3.8 7.8h1.3v4h2.2V9.5h1.4v2.3h2.2v-4h1.3z" fill="#fff"/></svg></li>
    </ul>
  </section>
</main>
</body>
</html>
```